Ridgeline Haul Carriers - Website

A clean, not cluttered informative website for our business. We specialize in the transportation of radioactive materials across North America. The site is mostly for information about our company and will not be used to attract business but will be used to attract employee's mainly drivers. Driver's are very hard to find in our area. One of the pages needs to be a job's posting page with an apply now button. Either an application can be filled out there or a resume can be uploaded which ever functionality works better. I would like a website that I can easily edit, ability to change text and photos.

Number of Pages Required

5+ page

Colors

Designer to choose colors to be used in the design.

Requirements
Must have
• Home - About - Services - Jobs - Contact pages
• A way prospective employee's can apply or upload their resume to be emailed to me
• Very clean apperance
Should not have
• I don't want it to be busy

```html
<!DOCTYPE html>
<html lang="en">
<head>
<meta charset="utf-8">
<title>Ridgeline Haul Carriers</title>
<link href="https://fonts.googleapis.com/css2?family=Exo+2:wght@500;600;700&family=Open+Sans:wght@400;600&display=swap" rel="stylesheet">
<style>
  :root {
    --red: #e30a1c;
    --red-deep: #b0061a;
    --ink: #111111;
    --text: #3a3a3a;
    --white: #ffffff;
    --footer: #e3e3e3;
    --ring: #cfcfcf;
    --heading: "Exo 2", Arial, sans-serif;
    --body: "Open Sans", Arial, sans-serif;
  }
  * { box-sizing: border-box; margin: 0; padding: 0; }
  html, body { width: 1200px; height: 2169px; overflow: hidden; background: var(--white); }
  body { position: relative; font-family: var(--body); color: var(--text); }

  .site-header { position: absolute; top: 0; left: 0; width: 1200px; height: 95px; background: var(--white); z-index: 3; }
  .brand { position: absolute; left: 160px; top: 30px; display: flex; align-items: center; gap: 10px;
    font-family: var(--heading); font-weight: 700; font-size: 26px; color: var(--red); letter-spacing: 0.5px; text-transform: uppercase; }
  .brand-dot { width: 22px; height: 22px; border-radius: 50%; background: var(--red); }
  .main-nav { position: absolute; top: 36px; right: 160px; display: flex; gap: 37px; }
  .main-nav a { font-family: var(--heading); font-weight: 600; font-size: 19px; color: var(--ink); text-decoration: none; }
  .main-nav a.active { color: var(--red); }

  .hero { position: absolute; top: 95px; left: 0; width: 1200px; height: 640px; }
  .hero-photo { position: absolute; inset: 0; background: linear-gradient(180deg, #6d6d6d 0%, #4a4a4c 45%, #2f3036 100%); }
  .hero-curve { position: absolute; left: 0; top: 0; }
  .hero-copy { position: absolute; top: 180px; left: 0; width: 1200px; text-align: center; color: var(--white); }
  .hero-kicker { font-family: var(--heading); font-weight: 700; font-size: 46px; line-height: 1; }
  .hero-title { font-family: var(--heading); font-weight: 700; font-size: 52px; line-height: 1.2; margin-top: 6px; text-transform: uppercase; }
  .hero-sub { font-family: var(--heading); font-weight: 500; font-size: 19px; line-height: 23px; margin-top: 12px; text-transform: uppercase; }
  .hero-arrow { position: absolute; top: 240px; }
  .hero-arrow.prev { left: 110px; }
  .hero-arrow.next { right: 110px; }
  .scroll-down { position: absolute; left: 574px; top: 392px; width: 52px; height: 52px; border-radius: 50%; background: var(--red); display: flex; align-items: center; justify-content: center; }

  .feature-cards { position: absolute; top: 632px; left: 168px; display: flex; gap: 21px; z-index: 2; }
  .feature-card { position: relative; width: 274px; height: 349px; border-radius: 52px; overflow: hidden; color: var(--white); text-align: center; }
  .feature-card .card-photo { position: absolute; inset: 0; background: linear-gradient(160deg, #f0243a 0%, var(--red) 50%, var(--red-deep) 100%); }
  .feature-card.muted .card-photo { background: linear-gradient(160deg, #8a8f97 0%, #6f7279 55%, #5b4e55 100%); }
  .card-icon { position: relative; margin-top: 30px; height: 56px; }
  .card-title { position: relative; font-family: var(--heading); font-weight: 700; font-size: 28px; margin-top: 10px; }
  .card-text { position: relative; font-size: 14px; line-height: 19.5px; padding: 0 26px; margin-top: 8px; }
  .card-link { position: absolute; left: 0; bottom: 0; width: 100%; height: 54px; background: var(--ink);
    display: flex; align-items: center; justify-content: center; gap: 6px;
    font-family: var(--heading); font-weight: 700; font-size: 17px; }
  .card-link .go { width: 18px; height: 18px; border-radius: 50%; background: var(--white); display: flex; align-items: center; justify-content: center; }

  .services-media { position: absolute; left: 170px; top: 1038px; width: 380px; height: 380px; border-radius: 50%; border: 6px solid var(--ring); padding: 13px; }
  .services-media .photo { width: 100%; height: 100%; border-radius: 50%; background: radial-gradient(circle at 35% 60%, #f39a3c 0%, #b5452a 30%, #3b2d34 65%, #1c1d24 100%); }
  .services-copy { position: absolute; left: 581px; top: 1083px; width: 450px; }
  .section-title { font-family: var(--heading); font-weight: 700; font-size: 33px; color: var(--red); }
  .services-copy p { font-size: 16px; line-height: 23.2px; margin-top: 22px; color: var(--text); }
  .btn-outline { display: inline-flex; align-items: center; justify-content: center; width: 165px; height: 46px; margin-top: 26px;
    border: 2px solid var(--red); border-radius: 3px; color: var(--red); font-family: var(--heading); font-weight: 700; font-size: 16px; text-decoration: none; }

  .jobs-banner { position: absolute; left: 0; top: 1470px; width: 1200px; height: 460px; }
  .jobs-back { position: absolute; left: 0; top: 0; }
  .jobs-panel { position: absolute; left: 161px; top: 32px; width: 884px; height: 395px; border-radius: 10px; overflow: hidden; color: var(--white); text-align: center; }
  .jobs-panel .photo { position: absolute; inset: 0; background: linear-gradient(100deg, #120306 0%, #5e0612 35%, #b80a1f 65%, #e8102a 100%); }
  .jobs-title { position: relative; font-family: var(--heading); font-weight: 700; font-size: 34px; margin-top: 96px; }
  .jobs-text { position: relative; font-size: 17px; line-height: 24.5px; margin-top: 10px; }
  .btn-light { position: relative; display: inline-flex; align-items: center; justify-content: center; width: 180px; height: 53px; margin-top: 28px;
    border: 2px solid var(--white); border-radius: 3px; color: var(--white); font-family: var(--heading); font-weight: 700; font-size: 18px; text-decoration: none; }

  .site-footer { position: absolute; left: 0; top: 2018px; width: 1200px; height: 151px; background: var(--footer); }
  .footer-nav { position: absolute; left: 177px; top: 41px; display: flex; gap: 34px; }
  .footer-nav a { font-family: var(--heading); font-weight: 600; font-size: 17px; color: #333; text-decoration: none; }
  .copyright { position: absolute; left: 177px; top: 78px; font-size: 13px; color: #444; }
  .social { position: absolute; left: 857px; top: 42px; display: flex; gap: 7px; }
  .social span { width: 35px; height: 35px; border-radius: 50%; border: 2px solid #222; }
</style>
</head>
<body>

<header class="site-header">
  <div class="brand"><span class="brand-dot"></span>Ridgeline Haul Carriers</div>
  <nav class="main-nav">
    <a class="active" href="#">HOME</a>
    <a href="#">ABOUT</a>
    <a href="#">SERVICES</a>
    <a href="#">JOBS</a>
    <a href="#">CONTACT</a>
  </nav>
</header>

<section class="hero">
  <div class="hero-photo" role="img" aria-label="Semi truck hauling cylindrical tanks on a flatbed beside a brick warehouse at dusk"></div>
  <svg class="hero-curve" width="1200" height="640" viewBox="0 0 1200 640">
    <path d="M0 580 Q600 520 1200 580 L1200 640 L0 640 Z" fill="#d4d4d4"/>
    <path d="M0 600 Q600 545 1200 610 L1200 640 L0 640 Z" fill="#ffffff"/>
  </svg>
  <svg class="hero-arrow prev" width="30" height="56" viewBox="0 0 30 56"><path d="M26 2 L4 28 L26 54" fill="none" stroke="#ffffff" stroke-width="3"/></svg>
  <svg class="hero-arrow next" width="30" height="56" viewBox="0 0 30 56"><path d="M4 2 L26 28 L4 54" fill="none" stroke="#ffffff" stroke-width="3"/></svg>
  <div class="hero-copy">
    <div class="hero-kicker">WELCOME TO</div>
    <h1 class="hero-title">Ridgeline Haul Carriers</h1>
    <p class="hero-sub">Ridgeline has been providing quality transportation<br>services since our founding in 1999.</p>
  </div>
  <a class="scroll-down" href="#">
    <svg width="22" height="14" viewBox="0 0 22 14"><path d="M3 3 L11 11 L19 3" fill="none" stroke="#111" stroke-width="4"/></svg>
  </a>
</section>

<div class="feature-cards">
  <article class="feature-card">
    <div class="card-photo" role="img" aria-label="Red-tinted photo of a truck driver"></div>
    <div class="card-icon">
      <svg width="56" height="56" viewBox="0 0 56 56"><circle cx="28" cy="28" r="25" fill="none" stroke="#fff" stroke-width="3"/><path d="M20 22 a8 8 0 1 1 11 7 c-3 1 -3 3 -3 6" fill="none" stroke="#fff" stroke-width="3.5"/><circle cx="28" cy="42" r="2.5" fill="#fff"/></svg>
    </div>
    <h2 class="card-title">ABOUT US</h2>
    <p class="card-text">Pellentesque faucibus Ut accumsan ultricies elit Maecenas at justo id velit placerat molestie Donec dictum lectus non odio Cras a ante vitae enim iaculis aliquam Mauris nunc</p>
    <a class="card-link" href="#">CLICK HERE <span class="go"><svg width="8" height="10" viewBox="0 0 8 10"><path d="M2 1 L6 5 L2 9" fill="none" stroke="#111" stroke-width="2"/></svg></span></a>
  </article>
  <article class="feature-card muted">
    <div class="card-photo" role="img" aria-label="Photo of a driver in a safety vest beside a truck"></div>
    <div class="card-icon">
      <svg width="56" height="56" viewBox="0 0 56 56"><path d="M50 6 L6 26 L22 32 L28 50 Z M50 6 L22 32" fill="none" stroke="#fff" stroke-width="3" stroke-linejoin="round"/></svg>
    </div>
    <h2 class="card-title">JOBS</h2>
    <p class="card-text">Pellentesque faucibus Ut accumsan ultricies elit Maecenas at justo id velit placerat molestie Donec dictum lectus non odio Cras a ante vitae enim iaculis aliquam Mauris nunc</p>
    <a class="card-link" href="#">CLICK HERE <span class="go"><svg width="8" height="10" viewBox="0 0 8 10"><path d="M2 1 L6 5 L2 9" fill="none" stroke="#111" stroke-width="2"/></svg></span></a>
  </article>
  <article class="feature-card">
    <div class="card-photo" role="img" aria-label="Red-tinted photo of a smiling driver in a plaid shirt"></div>
    <div class="card-icon">
      <svg width="60" height="56" viewBox="0 0 60 56"><path d="M4 4 L4 50 L58 50" fill="none" stroke="#fff" stroke-width="3"/><path d="M10 42 L24 26 L34 34 L52 14" fill="none" stroke="#fff" stroke-width="3"/><path d="M42 12 L54 12 L54 24" fill="none" stroke="#fff" stroke-width="3"/></svg>
    </div>
    <h2 class="card-title">CAREER</h2>
    <p class="card-text">Pellentesque faucibus Ut accumsan ultricies elit Maecenas at justo id velit placerat molestie Donec dictum lectus non odio Cras a ante vitae enim iaculis aliquam Mauris nunc</p>
    <a class="card-link" href="#">CLICK HERE <span class="go"><svg width="8" height="10" viewBox="0 0 8 10"><path d="M2 1 L6 5 L2 9" fill="none" stroke="#111" stroke-width="2"/></svg></span></a>
  </article>
</div>

<div class="services-media">
  <div class="photo" role="img" aria-label="Close-up of a red truck cab and wheels at sunset"></div>
</div>
<section class="services-copy">
  <h2 class="section-title">OUR SERVICES</h2>
  <p>We specialize in both expedited and regular LTL, Partial Load and Full Truck Load service between Canada, the USA. and Mexico. In addition, to meet our just in time door to door service requirements, our policy includes one line hauls right to your delivery, which eliminates extra handling of your products which also in turn reduces damages and claims.</p>
  <a class="btn-outline" href="#">READ MORE</a>
</section>

<section class="jobs-banner">
  <svg class="jobs-back" width="1200" height="460" viewBox="0 0 1200 460">
    <path d="M185 12 L1058 60 L1064 455 L155 430 Z" fill="#ec8a92"/>
    <path d="M185 12 L640 36 L185 36 Z" fill="#7a6a6e"/>
  </svg>
  <div class="jobs-panel">
    <div class="photo" role="img" aria-label="Red-tinted photo of a smiling driver behind the wheel"></div>
    <h2 class="jobs-title">AVAILABLE JOBS</h2>
    <p class="jobs-text">Aliquam Mauris nunc quam venenatis nec euismod sit amet egestas placerat est<br>Pellentesque habitant morbi tristique senectus et netus et malesuada<br>Fames ac turpis egestas Cras id elit Integer quis urna</p>
    <a class="btn-light" href="#">APPLY NOW</a>
  </div>
</section>

<footer class="site-footer">
  <nav class="footer-nav">
    <a href="#">HOME</a>
    <a href="#">ABOUT</a>
    <a href="#">SERVICES</a>
    <a href="#">JOBS</a>
    <a href="#">CONTACT</a>
  </nav>
  <p class="copyright">© 2019 COMPANY NAME &nbsp;ALL RIGHT RESERVED</p>
  <div class="social" aria-label="Social links">
    <span></span><span></span><span></span><span></span>
  </div>
</footer>

</body>
</html>
```